Business card for marketing analytics company

Need a business card for new company. I have a logo already that I want to be built into the card and should use those colours

Company is called steered by tallies
Design must bring steered by tallies to life not be a card that could be for anyone with a logo put on it.

Like the front to be fairly clean and uncluttered bringing the logo out with a suitable design on the back of the card.

The logo represents a compass and business growth so those themes along with numbers, analytics , data are appropriate.
I'm often working with creative industries so also needs to reflect the creative side of analytics rather than be very corporate looking.

Target Market(s)

Ad agency, media agency, consumer goods clients

Industry/Entity Type

Market Research

Contact Information for Business Card

Needs to include name, title, email and phone number

Colors
f78f20
f68d4d
ec1f27

Requirements
Must have
• Must bring steered by tallies to life not be a card that could be for anyone with a logo put on it.
• Logo, Correct colours
• Like a design on the back that relates to company name
• Designs for both sides
Should not have
• Please do not just submit logo and a coloured card.
• It needs to have a design element to it
• No black background
• No clear cards - needs front & back

```html
<!DOCTYPE html>
<html lang="en">
<head>
<meta charset="utf-8">
<title>Steered by Tallies – Business Card</title>
<link rel="stylesheet" href="https://fonts.googleapis.com/css2?family=Roboto:wght@400;500;700&display=swap">
<style>
  :root {
    --page-bg: #e6e6e6;
    --card-bg: #fbfbfb;
    --ink: #3d4852;
    --ink-soft: #4a4f55;
    --brand-red: #9b1f1d;
    --brand-orange: #d4601a;
    --accent-orange: #e8741c;
    --white: #ffffff;
    --faint-ring: #f1e6e2;
  }
  * { box-sizing: border-box; margin: 0; padding: 0; }
  html, body {
    width: 1200px; height: 576px; overflow: hidden;
    background: var(--page-bg);
    font-family: "Roboto", Arial, sans-serif;
  }
  .canvas { position: relative; width: 1200px; height: 576px; }

  .card {
    position: absolute; top: 138px;
    width: 484px; height: 292px;
    background: var(--card-bg);
    border-radius: 14px;
    overflow: hidden;
    box-shadow: 0 2px 6px rgba(0,0,0,0.12);
  }
  .card--front { left: 82px; }
  .card--back { left: 601px; }

  /* Brand lockup: plain circle + name in one colour and weight */
  .brand {
    position: absolute; display: flex; align-items: center;
  }
  .brand__dot { border-radius: 50%; background: var(--brand-orange); flex: none; }
  .brand__name {
    color: var(--ink); font-weight: 500; line-height: 1.05;
  }
  .card--front .brand { left: 98px; top: 98px; gap: 24px; }
  .card--front .brand__dot { width: 70px; height: 70px; }
  .card--front .brand__name { font-size: 29px; }

  .card--back .brand { left: 40px; top: 103px; gap: 16px; }
  .card--back .brand__dot { width: 44px; height: 44px; }
  .card--back .brand__name { font-size: 18px; }

  .back-ring { position: absolute; left: 0; top: 0; }

  .person { position: absolute; left: 271px; top: 72px; }
  .person__name { color: var(--brand-red); font-weight: 700; font-size: 19px; }
  .person__title { color: var(--ink-soft); font-size: 11px; margin-top: 5px; }

  .contacts { position: absolute; left: 275px; top: 130px; list-style: none; }
  .contacts li {
    display: flex; align-items: center; gap: 8px;
    color: var(--ink-soft); font-size: 11.5px; height: 16.5px;
  }
  .contacts svg { width: 11px; height: 11px; flex: none; }

  .bands { position: absolute; left: 0; top: 0; }
  .footer-web {
    position: absolute; left: 271px; top: 264px;
    color: var(--white); font-size: 11.5px;
  }
</style>
</head>
<body>
<main class="canvas">

  <section class="card card--front" aria-label="Card front">
    <div class="brand">
      <span class="brand__dot"></span>
      <span class="brand__name">Steered by<br>Tallies</span>
    </div>
  </section>

  <section class="card card--back" aria-label="Card back">
    <svg class="back-ring" width="484" height="292" aria-hidden="true">
      <circle cx="372" cy="134" r="104" fill="none" stroke="var(--faint-ring)" stroke-width="4"/>
    </svg>

    <div class="brand">
      <span class="brand__dot"></span>
      <span class="brand__name">Steered by<br>Tallies</span>
    </div>

    <div class="person">
      <h1 class="person__name">Mara T. Ellison</h1>
      <p class="person__title">Managing Director</p>
    </div>

    <ul class="contacts">
      <li>
        <svg viewBox="0 0 12 12" aria-hidden="true"><path fill="var(--accent-orange)" d="M1 4c0-2 2-3 5-3s5 1 5 3H8.5V3h-5v1H1zM2.5 5h7l1 6h-9z"/><circle cx="6" cy="8" r="1.4" fill="#fff"/></svg>
        1300 482 915
      </li>
      <li>
        <svg viewBox="0 0 12 12" aria-hidden="true"><circle cx="6" cy="6" r="5" fill="var(--accent-orange)"/><path d="M1 6h10M6 1c-2.5 2.5-2.5 7.5 0 10M6 1c2.5 2.5 2.5 7.5 0 10" stroke="#fff" stroke-width="0.8" fill="none"/></svg>
        www.steeredbytallies.com
      </li>
      <li>
        <svg viewBox="0 0 12 12" aria-hidden="true"><rect x="0.5" y="2.5" width="11" height="7.5" fill="var(--accent-orange)"/><path d="M0.8 2.8 6 7l5.2-4.2" stroke="#fff" stroke-width="0.9" fill="none"/></svg>
        hello@steeredbytallies.com
      </li>
    </ul>

    <svg class="bands" width="484" height="292" aria-hidden="true">
      <rect x="0" y="272" width="240" height="20" fill="var(--accent-orange)"/>
      <polygon points="234,254 484,254 484,292 210,292" fill="var(--brand-red)"/>
    </svg>
    <p class="footer-web">www.steeredbytallies.com</p>
  </section>

</main>
</body>
</html>
```